New Mechanical Maintenance business needs website

New Mechanical Maintenance business in Perth Western Australia needs a nice and easy to navigate website. Showing what we do and how we can be the right fit for other small to medium size business by offering personalized service from our highly skilled team. We deal with both fixed plant repairs like food and chemical processing facilities to heavy equipment like drill rigs, Large boats and earthmoving equipment.

Target Market(s)

Small to medium business to offer personalized services/packages

Industry/Entity Type

e deal with both fixed plant repairs like food and chemical processing facilities to heavy equipment like drill rigs, Large boats and earthmoving equipment.

Coding

Coded - Design and coding required

Number of Pages Required

4 page

Font styles to use
Serif

Colors
0054AA
0677BA
7BADD7
CADEEF
E8F1F8

Requirements
Must have
• A website that is easy to navigate but covers off on the range of services/maintenance we can provide

```html
<!DOCTYPE html>
<html lang="en">
<head>
<meta charset="utf-8">
<title>Ridgeway Maintenance</title>
<link href="https://fonts.googleapis.com/css2?family=Cabin:wght@500;600;700&family=Roboto:wght@400;500;700&display=swap" rel="stylesheet">
<style>
:root{
  --band:#4e5f84;
  --band-dark:#2f3d5e;
  --ink:#1a1a1a;
  --muted:#777;
  --btn:#555a60;
  --link:#0054aa;
  --light:#eeeeee;
  --footer:#000;
  --white:#fff;
}
*{box-sizing:border-box;margin:0;padding:0}
html,body{width:1200px;height:4132px;overflow:hidden}
body{position:relative;font-family:'Roboto',sans-serif;color:var(--ink);background:var(--white)}
.abs{position:absolute}
h1,h2,.heading{font-family:'Cabin',sans-serif;font-weight:600}

.topbar{left:0;top:0;width:1200px;height:40px;text-align:center;font-size:13px;line-height:40px;color:#555}
.topbar a{color:var(--link);text-decoration:none}

.hero{left:0;top:40px;width:1200px;height:603px;background:linear-gradient(100deg,#2c3f6e 0%,#41557f 45%,#6d7890 70%,#8a8274 100%)}
.brand{display:flex;align-items:center;gap:8px;color:var(--white);font-family:'Cabin',sans-serif;font-weight:700;font-size:22px;letter-spacing:2px}
.brand .dot{width:26px;height:26px;border-radius:50%;border:3px solid var(--white)}
.hero .brand{left:115px;top:63px}
.nav{left:477px;top:70px;display:flex;gap:38px;font-size:14px;color:var(--white)}
.social{top:68px;width:28px;height:28px;border-radius:50%;background:var(--white)}
.contact-btn{left:940px;top:60px;width:138px;height:42px;border-radius:21px;background:#555c66;color:var(--white);font-size:13px;font-weight:700;text-align:center;line-height:42px}
.hero h1{left:110px;top:238px;font-size:48px;line-height:57px;color:var(--white);width:560px}
.pill{height:42px;border-radius:21px;color:var(--white);font-size:13px;font-weight:700;display:flex;align-items:center;justify-content:center;gap:8px}
.get-started{left:110px;top:441px;width:156px;background:#555c66}
.phone-pill{left:290px;top:441px;width:204px;background:#5a6c95;justify-content:flex-start;padding-left:6px}
.phone-pill .ic{width:32px;height:32px;border-radius:50%;background:var(--white);display:flex;align-items:center;justify-content:center}

.fit{left:0;top:643px;width:1200px;height:343px;background:var(--band)}
.fit h2{position:absolute;top:48px;width:100%;text-align:center;font-size:38px;color:var(--white)}
.fit-item{position:absolute;width:340px;text-align:center;color:var(--white);font-weight:700;font-size:16px}
.fit-item .circle{margin:0 auto 18px;border-radius:50%;background:var(--white);display:flex;align-items:center;justify-content:center}

.about-img{left:111px;top:1080px;width:415px;height:372px;background:linear-gradient(135deg,#c99b4e,#4b6f95 55%,#d8673a)}
.badge{left:427px;top:1120px;width:134px;height:135px;background:var(--white);text-align:center;box-shadow:0 4px 14px rgba(0,0,0,.15);padding-top:24px}
.badge .num{font-family:'Cabin',sans-serif;font-size:48px;font-weight:600;line-height:1}
.badge .num small{font-size:15px}
.badge .lbl{font-weight:700;font-size:17px;margin-top:10px}
.about-title{left:617px;top:1072px;font-size:36px}
.about-text{left:617px;top:1134px;width:469px;font-size:13px;line-height:25.6px;color:var(--muted);text-align:justify}
.about-text p+p{margin-top:16px}
.btn{background:var(--btn);color:var(--white);font-size:13px;font-weight:700;border-radius:22px;display:flex;align-items:center;justify-content:center;gap:8px}
.view-more{left:617px;top:1410px;width:156px;height:43px}

.services{left:0;top:1541px;width:1200px;height:1121px;background:var(--light)}
.services h2{position:absolute;left:110px;top:80px;font-size:36px}
.card{position:absolute;width:300px}
.card .ph{width:295px;height:251px}
.card h3{font-size:15px;font-weight:500;margin-top:22px}
.card p{font-size:13px;line-height:26px;color:var(--muted);margin-top:11px;text-align:justify;width:285px}
.quote-btn{left:114px;top:995px;width:286px;height:44px}

.clients{left:0;top:2662px;width:1200px;height:363px;background:var(--band)}
.clients h2{position:absolute;top:62px;width:100%;text-align:center;font-size:36px;color:var(--white)}
.clients .quote{position:absolute;left:220px;top:150px;width:760px;text-align:center;color:var(--white);font-size:13px;line-height:30px}
.clients .who{position:absolute;top:258px;width:100%;text-align:center;color:#e6e9f0;font-size:13px}
.arrow{position:absolute;top:164px;width:48px;height:48px;border-radius:50%;background:var(--white);color:#333;text-align:center;line-height:46px;font-size:18px}

.work-title{top:3098px;width:1200px;text-align:center;font-size:36px}
.tile{position:absolute}

.footer{left:0;top:3815px;width:1200px;height:317px;background:var(--footer);color:var(--white)}
.footer .brand{left:151px;top:84px;font-size:26px}
.footer .brand .dot{width:34px;height:34px}
.fcol{position:absolute;top:92px;font-size:13px;line-height:26px}
.fcol h4{font-size:14px;font-weight:700;margin-bottom:14px;line-height:20px}
.fcol .row{display:flex;align-items:center;gap:12px;margin-bottom:10px}
.fcol .ico{width:20px;height:20px;border-radius:50%;background:var(--white);display:flex;align-items:center;justify-content:center}
.copy{position:absolute;top:256px;width:100%;text-align:center;font-size:12px}
</style>
</head>
<body>

<div class="abs topbar">Call Us Today on <a>+61 (8) 5550 1234</a> for a free onsite quotation or email <a>hello@ridgewaymaint.com</a></div>

<header class="abs hero" role="img" aria-label="Welder in hard hat and hi-vis vest working on steel mesh with sparks">
</header>
<div class="abs brand" style="left:115px;top:88px"><span class="dot"></span>RIDGEWAY</div>
<nav class="abs nav"><span>Home</span><span>About</span><span>Services</span><span>Work</span></nav>
<span class="abs social" style="left:789px"></span>
<span class="abs social" style="left:832px"></span>
<span class="abs social" style="left:875px"></span>
<div class="abs contact-btn">CONTACT US</div>
<h1 class="abs" style="left:110px;top:238px;font-size:48px;line-height:57px;color:#fff;width:560px">Specialists In Engineering, Maintenance &amp; Support Services</h1>
<div class="abs pill get-started">GET STARTED
  <svg width="12" height="12" viewBox="0 0 12 12"><circle cx="6" cy="6" r="6" fill="#fff"/><path d="M5 3.5 7.5 6 5 8.5" stroke="#555c66" stroke-width="1.6" fill="none"/></svg></div>
<div class="abs pill phone-pill"><span class="ic"><svg width="16" height="16" viewBox="0 0 24 24"><path d="M6.6 10.8a15 15 0 0 0 6.6 6.6l2.2-2.2c.3-.3.7-.4 1-.2 1.1.4 2.3.6 3.6.6.6 0 1 .4 1 1V20c0 .6-.4 1-1 1A17 17 0 0 1 3 4c0-.6.4-1 1-1h3.5c.6 0 1 .4 1 1 0 1.3.2 2.5.6 3.6.1.3 0 .7-.2 1z" fill="#333"/></svg></span>+61 (8) 5550 1234</div>

<section class="abs fit">
  <h2>HOW WE CAN BE FIT</h2>
  <div class="fit-item" style="left:60px;top:133px">
    <div class="circle" style="width:90px;height:90px"><svg width="44" height="44" viewBox="0 0 24 24"><path d="M6.6 10.8a15 15 0 0 0 6.6 6.6l2.2-2.2c.3-.3.7-.4 1-.2 1.1.4 2.3.6 3.6.6.6 0 1 .4 1 1V20c0 .6-.4 1-1 1A17 17 0 0 1 3 4c0-.6.4-1 1-1h3.5c.6 0 1 .4 1 1 0 1.3.2 2.5.6 3.6.1.3 0 .7-.2 1z" fill="none" stroke="#4e5f84" stroke-width="1.6"/></svg></div>
    JUST A PHONE CALL AWAY</div>
  <div class="fit-item" style="left:415px;top:138px">
    <div class="circle" style="width:118px;height:118px;border:10px solid #9aa3b5">
      <svg width="60" height="60" viewBox="0 0 60 60"><circle cx="30" cy="30" r="27" fill="#4e5f84"/><circle cx="30" cy="30" r="18" fill="none" stroke="#fff" stroke-width="3"/><path d="M22 30l6 6 11-12" stroke="#fff" stroke-width="4" fill="none"/></svg></div>
    HIGHLY QUALIFIED TRADES</div>
  <div class="fit-item" style="left:770px;top:133px">
    <div class="circle" style="width:90px;height:90px"><svg width="54" height="50" viewBox="0 0 54 50"><path d="M27 2 39 16h-7v14H22V16h-7z" fill="#4e5f84"/><path d="M12 14 20 23h-5v7H9v-7H4zM42 14l8 9h-5v7h-6v-7h-5z" fill="#4e5f84"/><text x="27" y="46" text-anchor="middle" font-family="Roboto,sans-serif" font-size="13" font-weight="700" fill="#4e5f84">COST</text></svg></div>
    HIGHLY COST-EFFECTIVE TACTICS</div>
</section>

<div class="abs about-img" role="img" aria-label="Smiling team of workers in hard hats and hi-vis vests"></div>
<div class="abs badge"><div class="num">20<small>Yrs</small></div><div class="lbl">EXPERIENCE</div></div>
<h2 class="abs about-title">About Us</h2>
<div class="abs about-text">
  <p>Lorem ipsum dolor sit amet, consectetur adipiscing elit, sed do eiusmod tempor incididunt ut labore et dolore magna aliqua. Ut enim ad minim veniam, quis nostrud exercitation ullamco laboris nisi ut aliquip ex ea commodo consequat. Duis aute irure dolor in reprehenderit in voluptate velit esse cillum dolore eu fugiat nulla pariatur. Excepteur sint occaecat cupidatat non proident, sunt in culpa qui officia deserunt.</p>
  <p>Lorem ipsum dolor sit amet, consectetur adipiscing elit, sed do eiusmod tempor incididunt ut labore et dolore magna aliqua. Ut enim ad minim veniam, quis nostrud exercitation .</p>
</div>
<div class="abs btn view-more">VIEW MORE <svg width="12" height="12" viewBox="0 0 12 12"><circle cx="6" cy="6" r="6" fill="#fff"/><path d="M5 3.5 7.5 6 5 8.5" stroke="#555a60" stroke-width="1.6" fill="none"/></svg></div>

<section class="abs services">
  <h2>Services We Offer</h2>
  <div class="card" style="left:114px;top:164px"><div class="ph" role="img" aria-label="Technician working on gear machinery" style="background:linear-gradient(135deg,#cfd2d6,#7b7f86 60%,#2f5fa4)"></div><h3>Fixed Plant Mechanical &amp; Maintenance</h3><p>Lorem ipsum dolor sit amet, consectetur adipiscing elit, sed do eiusmod tempor incididunt ut labore</p></div>
  <div class="card" style="left:453px;top:164px"><div class="ph" role="img" aria-label="Buildings under construction with cranes and excavator" style="background:linear-gradient(180deg,#dfe4ea,#a8a9aa 55%,#6d6a66)"></div><h3>Sustaining Capital &amp; Minor Projects</h3><p>Lorem ipsum dolor sit amet, consectetur adipiscing elit, sed do eiusmod tempor incididunt ut labore</p></div>
  <div class="card" style="left:792px;top:164px"><div class="ph" role="img" aria-label="Machinist operating a lathe" style="background:linear-gradient(135deg,#2f5a46,#7d8176 50%,#b9bcbd)"></div><h3>Rotating Equipment &amp; On-Site Machining</h3><p>Lorem ipsum dolor sit amet, consectetur adipiscing elit, sed do eiusmod tempor incididunt ut labore</p></div>
  <div class="card" style="left:114px;top:583px"><div class="ph" role="img" aria-label="CNC laser cutting steel with sparks" style="background:linear-gradient(135deg,#4a6a8a,#c88a3c 55%,#3a3a3c)"></div><h3>Workshop Fabrication &amp; CNC Machining</h3><p>Lorem ipsum dolor sit amet, consectetur adipiscing elit, sed do eiusmod tempor incididunt ut labore</p></div>
  <div class="card" style="left:453px;top:583px"><div class="ph" role="img" aria-label="Offshore oil platform lit at dusk" style="background:linear-gradient(180deg,#4a79a8,#c98a46 55%,#3f6f92)"></div><h3>NPI &amp; Facilities Maintenance Services</h3><p>Lorem ipsum dolor sit amet, consectetur adipiscing elit, sed do eiusmod tempor incididunt ut labore</p></div>
  <div class="card" style="left:792px;top:583px"><div class="ph" role="img" aria-label="Engineer with tablet inspecting industrial pipework" style="background:linear-gradient(135deg,#b8b4b3,#6b6d74 50%,#3d5e7a)"></div><h3>In-House Specialist Coatings</h3><p>Lorem ipsum dolor sit amet, consectetur adipiscing elit, sed do eiusmod tempor incididunt ut labore</p></div>
  <div class="abs btn quote-btn">CONTACT US FOR A FREE QUOTE <svg width="12" height="12" viewBox="0 0 12 12"><circle cx="6" cy="6" r="6" fill="#fff"/><path d="M5 3.5 7.5 6 5 8.5" stroke="#555a60" stroke-width="1.6" fill="none"/></svg></div>
</section>

<section class="abs clients">
  <h2>Our Clients</h2>
  <div class="arrow" style="left:31px">‹</div>
  <div class="arrow" style="left:1101px">›</div>
  <p class="quote">Lorem ipsum dolor sit amet, consectetur adipiscing elit, sed do eiusmod tempor incididunt ut labore et dolore magna aliqua. Ut enim ad minim veniam, quis nostrud exercitation ullamco laboris nisi ut aliquip ex ea commodo consequat. Duis aute irure dolor in reprehenderit in voluptate velit esse cillum dolore eu fugiat nulla pariatur.</p>
  <p class="who">— Grace from Perth</p>
</section>

<h2 class="abs work-title">Our Work</h2>
<div class="tile" style="left:88px;top:3176px;width:241px;height:268px;background:linear-gradient(180deg,#6d9ccc,#8c8b86 60%,#4d4a46)" role="img" aria-label="Refinery towers against blue sky"></div>
<div class="tile" style="left:345px;top:3176px;width:240px;height:268px;background:linear-gradient(135deg,#6e8a6c,#c8593a 55%,#6e5d4c)" role="img" aria-label="Excavator on a hillside site"></div>
<div class="tile" style="left:603px;top:3176px;width:239px;height:268px;background:linear-gradient(135deg,#1f4e7c,#a66a3c 50%,#2c6b9c)" role="img" aria-label="Mechanic servicing a brake disc"></div>
<div class="tile" style="left:860px;top:3176px;width:240px;height:268px;background:linear-gradient(180deg,#9aa4ad,#2f3d5a 70%,#5e5f63)" role="img" aria-label="Crew of engineers in hard hats at a shipyard"></div>
<div class="tile" style="left:88px;top:3461px;width:241px;height:268px;background:linear-gradient(135deg,#7e7b74,#c77a3a 45%,#3a73a6)" role="img" aria-label="Worker rigging large pipes"></div>
<div class="tile" style="left:345px;top:3461px;width:497px;height:268px;background:linear-gradient(135deg,#2f6170,#4b5f5f 50%,#8a7a5e)" role="img" aria-label="Workshop floor with workers fabricating parts"></div>
<div class="tile" style="left:860px;top:3461px;width:240px;height:268px;background:linear-gradient(135deg,#9c9894,#5a4034 55%,#2e2b2a)" role="img" aria-label="Large steel pipe on a workshop floor"></div>

<footer class="abs footer">
  <div class="abs brand"><span class="dot"></span>RIDGEWAY</div>
  <div class="fcol" style="left:364px"><h4>LOCATION</h4>Lorem ipsum dolor sit amet,<br>consectetur adipiscing elit,<br>sed do eiusmod tempor</div>
  <div class="fcol" style="left:654px"><h4>CONTACT</h4>
    <div class="row"><span class="ico"><svg width="12" height="12" viewBox="0 0 24 24"><path d="M6.6 10.8a15 15 0 0 0 6.6 6.6l2.2-2.2c.3-.3.7-.4 1-.2 1.1.4 2.3.6 3.6.6.6 0 1 .4 1 1V20c0 .6-.4 1-1 1A17 17 0 0 1 3 4c0-.6.4-1 1-1h3.5c.6 0 1 .4 1 1 0 1.3.2 2.5.6 3.6.1.3 0 .7-.2 1z" fill="#000"/></svg></span>+61 (8) 5550 1234</div>
    <div class="row"><span class="ico"><svg width="12" height="10" viewBox="0 0 12 10"><rect x=".5" y=".5" width="11" height="9" fill="none" stroke="#000"/><path d="M.5 .5 6 5.5 11.5 .5" stroke="#000" fill="none"/></svg></span>hello@ridgewaymaint.com</div>
  </div>
  <div class="fcol" style="left:980px"><h4>QUICK LINKS</h4>Home<br>Service<br>About<br>Contact</div>
  <p class="copy">Copyright@2024 - All Rights Reserved by Ridgeway Services</p>
</footer>

</body>
</html>
```